Brake Test Training for Coal Mining

We offer Brake Test Training for Coal Mine workers. It's a legislative requirement that workers who are tasked with performing brake testing have certain competencies to do so. We test Light Vehicles and trailers, Heavy Vehicles and Mobile Mining Equipment like Graders, Scrapers and Dump Trucks.

```html
<!DOCTYPE html>
<html lang="en">
<head>
<meta charset="UTF-8">
<title>Brake Test Training Billboard</title>
<link href="https://fonts.googleapis.com/css2?family=Poppins:wght@500;600;700;800&display=swap" rel="stylesheet">
<style>
  :root {
    --navy: #163a5f;
    --navy-deep: #12304f;
    --yellow: #f7c600;
    --ink: #111111;
    --white: #ffffff;
    --page: #eeeeee;
  }
  * { margin: 0; padding: 0; box-sizing: border-box; }
  html, body { width: 859px; height: 1200px; overflow: hidden; }
  body { background: var(--page); font-family: "Poppins", sans-serif; position: relative; }

  .billboard {
    position: absolute; left: 29px; top: 420px;
    width: 800px; height: 360px;
    background: var(--white);
    overflow: hidden;
    box-shadow: 0 6px 22px rgba(0,0,0,0.18);
  }
  .billboard > * { position: absolute; }

  .headline {
    left: 25px; top: 6px;
    font-size: 45px; font-weight: 700; color: var(--navy);
    letter-spacing: -0.5px; line-height: 1.1;
  }
  .audience-band {
    left: 0; top: 63px; width: 572px; height: 34px;
    background: var(--yellow);
  }
  .audience {
    left: 25px; top: 63px; line-height: 34px;
    font-size: 27px; font-weight: 700; color: var(--ink);
  }
  .intro-bar { left: 26px; top: 108px; width: 5px; height: 38px; background: var(--yellow); border-radius: 3px; }
  .intro {
    left: 42px; top: 104px;
    font-size: 17px; font-weight: 600; color: var(--ink); line-height: 22px;
  }

  .services-band {
    left: 0; top: 154px; width: 800px; height: 128px;
    background: linear-gradient(90deg, var(--navy-deep), var(--navy));
  }
  .tab { left: 0; top: 154px; }
  .tab-label {
    left: 27px; top: 154px; line-height: 34px;
    font-size: 23px; font-weight: 700; color: var(--navy); letter-spacing: 3px;
  }
  .check {
    font-size: 14px; font-weight: 600; color: var(--white);
    display: flex; align-items: flex-start; gap: 6px; line-height: 18px;
  }
  .check svg { flex: none; margin-top: 4px; }
  .check-light { left: 26px; top: 196px; }
  .check-trailers { left: 182px; top: 196px; }
  .check-heavy { left: 277px; top: 196px; }
  .check-mining { left: 26px; top: 228px; }

  .tag {
    background: var(--yellow); color: var(--ink);
    font-size: 11px; font-weight: 600; text-align: center;
    height: 17px; line-height: 17px;
  }
  .tag-graders { left: 197px; top: 230px; width: 73px; }
  .tag-scrapers { left: 274px; top: 230px; width: 73px; }
  .tag-dump { left: 197px; top: 253px; width: 150px; }

  .machine-photo {
    left: 405px; top: 70px; width: 395px; height: 234px;
    background: linear-gradient(135deg, rgba(230,230,230,0.2) 0%, #f0b51d 45%, #d98a1c 75%, #3a3a3a 100%);
    border-radius: 4px;
  }

  .phone-icon { left: 23px; top: 294px; }
  .phone {
    left: 84px; top: 282px;
    font-size: 55px; font-weight: 700; color: var(--ink); letter-spacing: -1px; line-height: 66px;
  }
  .web-band {
    left: 464px; top: 304px; width: 336px; height: 26px;
    background: var(--yellow); border-radius: 13px 0 0 13px;
  }
  .web {
    left: 474px; top: 304px; width: 320px; line-height: 26px; text-align: center;
    font-size: 20px; font-weight: 700; color: var(--ink); letter-spacing: 5px;
  }

  .brand { left: 604px; top: 20px; display: flex; align-items: center; gap: 10px; }
  .brand-mark { width: 22px; height: 22px; border-radius: 50%; background: var(--navy); }
  .brand-name {
    font-size: 11px; font-weight: 700; color: var(--navy); line-height: 13px; text-transform: uppercase;
    border-top: 2px solid var(--navy); border-bottom: 2px solid var(--yellow); padding: 3px 2px;
  }
</style>
</head>
<body>
  <section class="billboard">
    <div class="machine-photo" role="img" aria-label="Photo of a yellow wheel loader with raised bucket"></div>

    <h1 class="headline">BRAKE TEST TRAINING</h1>
    <div class="audience-band"></div>
    <h2 class="audience">FOR COAL MINING WORKERS</h2>
    <div class="intro-bar"></div>
    <p class="intro">Workers testing brakes must meet required<br>competencies as per legislation.</p>

    <div class="brand">
      <span class="brand-mark"></span>
      <span class="brand-name">Ridgeline Operator Training</span>
    </div>

    <div class="services-band"></div>
    <svg class="tab" width="200" height="34" viewBox="0 0 200 34">
      <path d="M0 0 H200 L185 34 H0 Z" fill="#f7c600"/>
    </svg>
    <div class="tab-label">WE TEST</div>

    <div class="check check-light"><svg width="9" height="9" viewBox="0 0 9 9"><rect width="9" height="9" rx="1.5" fill="#f7c600"/><path d="M2 4.6 L3.8 6.3 L7 2.8" stroke="#163a5f" stroke-width="1.4" fill="none"/></svg>Light Vehicles</div>
    <div class="check check-trailers"><svg width="9" height="9" viewBox="0 0 9 9"><rect width="9" height="9" rx="1.5" fill="#f7c600"/><path d="M2 4.6 L3.8 6.3 L7 2.8" stroke="#163a5f" stroke-width="1.4" fill="none"/></svg>Trailers</div>
    <div class="check check-heavy"><svg width="9" height="9" viewBox="0 0 9 9"><rect width="9" height="9" rx="1.5" fill="#f7c600"/><path d="M2 4.6 L3.8 6.3 L7 2.8" stroke="#163a5f" stroke-width="1.4" fill="none"/></svg>Heavy Vehicles</div>
    <div class="check check-mining"><svg width="9" height="9" viewBox="0 0 9 9"><rect width="9" height="9" rx="1.5" fill="#f7c600"/><path d="M2 4.6 L3.8 6.3 L7 2.8" stroke="#163a5f" stroke-width="1.4" fill="none"/></svg>Mobile Mining<br>Equipment</div>

    <div class="tag tag-graders">Graders</div>
    <div class="tag tag-scrapers">Scrapers</div>
    <div class="tag tag-dump">Dump Trucks</div>

    <svg class="phone-icon" width="38" height="38" viewBox="0 0 38 38">
      <circle cx="19" cy="19" r="19" fill="#f7c600"/>
      <path d="M13 11 l4 -1 2 5 -2.5 1.5 a11 11 0 0 0 5 5 l1.5 -2.5 5 2 -1 4 c-8 1 -15 -6 -14 -14 z" fill="#ffffff"/>
    </svg>
    <div class="phone">1300 555 018</div>
    <div class="web-band"></div>
    <div class="web">www.rlo.net.au</div>
  </section>
</body>
</html>
```